Professional Website for Leading Global Private Equity Real Estate Company

The company is a leading global Private Equity Real Estate (PERE). We need a homepage design, an inner page design, and color/font tweaks to the logo (color should be more soothing than current blue used in the logo). The logo website should project the company as global, professional, experienced, trustworthy, accessible, YOUNG, DYNAMIC, hi-tech. PLEASE SEE the attached Design Brief Word Doc for details.

Target Market(s)

institional investors and wealthy private individuals

Industry/Entity Type

Finance

Number of Pages Required

2 page

Font styles to use
Sans Serif
Other font styles liked:
• either like in https://www.ferndalequay.com/ or like in presentations (Montserrat Black & Montserrat Light, Century Gothic, Blair ITC, Almoni Neue DL 4.0 AAA Medium, Almoni DL AAA)

Requirements
Must have
• new color palette that is NOT based on current logo. they want a more soothing color palette than the blue in that logo. the new color palette should project: global, professional, experienced, trustworthy, accessible, YOUNG, DYNAMIC, hi-tech.
Nice to have
• the likes these sites: https://www.ferndalequay.com/ and https://www.tvr.law/

```html
<!DOCTYPE html>
<html lang="en">
<head>
<meta charset="utf-8">
<title>Veltora Real Estate</title>
<link href="https://fonts.googleapis.com/css2?family=Poppins:wght@300;400;500;600;700&display=swap" rel="stylesheet">
<style>
:root{
  --navy:#0e4a69;
  --navy-deep:#0a3a54;
  --sky:#3fb9f2;
  --sky-soft:#8fd6f7;
  --ink:#1d1d1d;
  --text:#555b61;
  --mist:#ececec;
  --white:#ffffff;
}
*{box-sizing:border-box;margin:0;padding:0}
html,body{width:1200px;height:4472px;overflow:hidden}
body{font-family:'Poppins',sans-serif;color:var(--text);background:var(--white);position:relative}
section,header,footer{position:absolute;left:0;width:1200px}
p{font-size:15px;line-height:27px}
.btn{display:inline-block;background:var(--sky);color:var(--white);font-weight:600;font-size:15px;padding:0 36px;height:54px;line-height:54px;border-radius:3px;box-shadow:0 6px 14px rgba(0,0,0,.18)}
h2{font-weight:500;color:var(--ink);font-size:46px}

/* hero */
.hero{top:0;height:650px}
.hero-photo{position:absolute;inset:0;background:linear-gradient(180deg,#5e7f93 0%,#8b8f8a 40%,#6b5a4a 75%,#3d4446 100%)}
.hero-shade{position:absolute;inset:0;background:rgba(10,40,60,.35)}
.nav{position:absolute;top:0;left:0;width:1200px;height:76px;display:flex;align-items:center;padding:0 110px}
.brand{display:flex;align-items:center;gap:10px;color:var(--white);font-weight:600;font-size:17px;letter-spacing:.5px}
.brand-dot{width:22px;height:22px;border-radius:50%;background:var(--sky)}
.menu{margin-left:auto;display:flex;gap:8px;align-items:center}
.menu a{color:var(--white);font-size:14px;padding:8px 14px;text-decoration:none}
.menu a.current{background:var(--sky);border-radius:2px}
.hero-title{position:absolute;top:250px;width:100%;text-align:center;color:var(--white);font-weight:600;font-size:60px}
.hero-lead{position:absolute;top:330px;left:300px;width:600px;text-align:center;color:var(--white);font-size:14px;line-height:24px}
.hero .btn{position:absolute;top:418px;left:532px;width:136px;padding:0;text-align:center}

/* about */
.about{top:650px;height:490px;text-align:center}
.about h2{margin-top:60px}
.about p{width:920px;margin:22px auto 0}
.counters{display:flex;justify-content:center;gap:62px;margin-top:34px}
.counter{width:100px;height:118px;background:var(--sky);border-radius:4px;color:var(--white);padding-top:18px}
.counter b{display:block;font-size:44px;font-weight:600;line-height:50px}
.counter span{font-size:12px}

/* platforms */
.platforms{top:1140px;height:680px;background:var(--navy)}
.platforms h2{color:var(--white);text-align:center;margin-top:70px}
.cards{position:absolute;top:160px;left:104px;display:flex;gap:20px}
.card{width:232px;height:380px;border:1px solid rgba(255,255,255,.4);text-align:center;color:var(--white)}
.card-photo{height:230px;margin:0}
.card h3{font-size:13px;font-weight:600;margin-top:10px}
.card p{font-size:11px;line-height:17px;padding:6px 20px 0;color:#cfe0ea}
.card .more{display:block;font-size:12px;font-weight:600;margin-top:10px}
.dots{position:absolute;top:1590px;left:0}
.slider-dots{position:absolute;top:592px;left:570px;display:flex;gap:6px}
.slider-dots i{width:12px;height:12px;border-radius:50%;border:2px solid var(--white)}
.slider-dots i.on{background:var(--white)}

/* edge */
.edge{top:1820px;height:700px}
.edge-text{position:absolute;left:112px;top:160px;width:470px}
.edge-text p{font-size:13px;line-height:24px;margin-top:18px}
.edge-text .btn{margin-top:34px;font-size:13px;height:52px;line-height:52px;padding:0 30px}
.edge-bar{position:absolute;top:76px;left:980px;width:220px;height:18px;background:var(--sky)}
.edge-frame{position:absolute;top:96px;left:612px;width:540px;height:480px;border:1px solid var(--sky-soft)}
.edge-photo{position:absolute;top:100px;left:632px;width:510px;height:420px;background:linear-gradient(135deg,#e9eef0 0%,#b7a995 45%,#3d3f47 100%)}

/* newsletter */
.news{top:2528px;height:224px;background:var(--navy)}
.news-kicker{position:absolute;left:112px;top:48px;color:var(--white);font-weight:600;font-size:19px}
.news-title{position:absolute;left:112px;top:88px;color:var(--white);font-weight:600;font-size:38px;line-height:42px}
.news-plane{position:absolute;left:392px;top:52px}
.field-line{position:absolute;top:96px;color:var(--white);font-size:14px;border-bottom:1px solid rgba(255,255,255,.7);padding-bottom:12px}

/* responsibility */
.resp{top:2800px;height:660px}
.resp-bar{position:absolute;top:52px;left:0;width:440px;height:18px;background:var(--sky)}
.resp-frame{position:absolute;top:72px;left:20px;width:570px;height:540px;border:1px solid var(--sky-soft)}
.resp-photo{position:absolute;top:76px;left:0;width:566px;height:520px;background:linear-gradient(135deg,#c9ccc6 0%,#8b7966 45%,#2e3a4a 100%)}
.resp-text{position:absolute;left:610px;top:132px;width:490px}
.resp-text p{font-size:13px;line-height:24px;margin-top:18px}
.resp-text .btn{margin-top:30px;font-size:14px;padding:0 40px}

/* contact */
.contact{top:3488px;height:552px;background:var(--mist);text-align:center}
.contact h2{margin-top:54px;font-size:44px}
.contact .lead{width:700px;margin:18px auto 0;font-size:13px;line-height:22px}
.form{position:absolute;top:196px;left:228px;width:744px}
.input{position:absolute;font-size:13px;color:var(--text);text-align:left;border-bottom:1px solid #777;height:30px;width:352px}
.form .btn{position:absolute;top:272px;left:267px;width:210px;padding:0;text-align:center;height:56px;line-height:56px;font-size:15px}

/* footer */
.site-foot{top:4040px;height:432px}
.foot-col{position:absolute;top:56px}
.foot-col h4{font-size:13px;font-weight:600;color:var(--ink);margin-bottom:14px}
.foot-col a{display:block;font-size:13px;line-height:32px;color:var(--text);text-decoration:none}
.contact-row{display:flex;align-items:center;gap:10px;font-size:13px;line-height:32px}
.socials{position:absolute;top:166px;left:912px;display:flex;gap:14px}
.socials i{width:26px;height:26px;background:var(--navy)}
.legal{position:absolute;top:310px;width:1200px;border-top:1px solid #ddd;padding-top:22px;text-align:center;font-size:13px;color:var(--ink)}
</style>
</head>
<body>

<header class="hero">
  <div class="hero-photo" role="img" aria-label="Aerial view of a suburban residential neighbourhood with homes and trees"></div>
  <div class="hero-shade"></div>
  <nav class="nav">
    <div class="brand"><span class="brand-dot"></span>VELTORA REAL ESTATE</div>
    <div class="menu">
      <a class="current">Home</a><a>About us</a><a>Our Businesses ▾</a><a>Investor Lobby</a><a>News</a><a>Contact Us</a>
      <svg width="14" height="14" viewBox="0 0 14 14"><circle cx="7" cy="4" r="3.2" fill="#fff"/><path d="M1 14c0-4 3-6 6-6s6 2 6 6z" fill="#fff"/></svg>
    </div>
  </nav>
  <h1 class="hero-title">Veltora Real Estate</h1>
  <p class="hero-lead">Lorem ipsum dolor sit amet, consectetur adipiscing elit, sed do eiusmod tempor incididunt ut labore et dolore magna aliqua. Ut enim ad minim veniam, quis nostrud.</p>
  <span class="btn">About Us</span>
</header>

<section class="about">
  <h2>About Us</h2>
  <p>Lorem ipsum dolor sit amet, consectetur adipiscing elit, sed do eiusmod tempor incididunt ut labore et dolore magna aliqua. Ut enim ad minim veniam, quis nostrud exercitation ullamco laboris nisi ut aliquip ex ea commodo consequat. Duis aute irure dolor in reprehenderit in voluptate velit esse cillum dolore eu fugiat nulla pariatur. Excepteur sint occaecat cupidatat non proident, sunt in culpa qui officia deserunt mollit anim id est laborum.</p>
  <div class="counters">
    <div class="counter"><b>20</b><span>Days</span></div>
    <div class="counter"><b>22</b><span>Hours</span></div>
    <div class="counter"><b>45</b><span>Minutes</span></div>
    <div class="counter"><b>59</b><span>Seconds</span></div>
  </div>
</section>

<section class="platforms">
  <h2>Our Investment Platforms</h2>
  <div class="cards">
    <article class="card"><div class="card-photo" role="img" aria-label="Hands signing a property contract" style="background:linear-gradient(135deg,#d9c3ad,#7b5a44)"></div><h3>Lorem ipsum dolor sit amet</h3><p>Lorem ipsum dolor consectetur adipiscing elit, sed do tempor ut labore et dolore magna aliqua</p><span class="more">Read More</span></article>
    <article class="card"><div class="card-photo" role="img" aria-label="House with a for sale sign in the front garden" style="background:linear-gradient(135deg,#9fb88a,#c24a3c 70%,#5b4a3a)"></div><h3>Lorem ipsum dolor sit amet</h3><p>Lorem ipsum dolor consectetur adipiscing elit, sed do tempor ut labore et dolore magna aliqua</p><span class="more">Read More</span></article>
    <article class="card"><div class="card-photo" role="img" aria-label="Desk with calculator and financial documents" style="background:linear-gradient(135deg,#e8e2d6,#9c8b72)"></div><h3>Lorem ipsum dolor sit amet</h3><p>Lorem ipsum dolor consectetur adipiscing elit, sed do tempor ut labore et dolore magna aliqua</p><span class="more">Read More</span></article>
    <article class="card"><div class="card-photo" role="img" aria-label="Couple meeting a real estate agent" style="background:linear-gradient(135deg,#e6ddd2,#8a6a57)"></div><h3>Lorem ipsum dolor sit amet</h3><p>Lorem ipsum dolor consectetur adipiscing elit, sed do tempor ut labore et dolore magna aliqua</p><span class="more">Read More</span></article>
  </div>
  <div class="slider-dots"><i class="on"></i><i></i><i></i><i></i></div>
</section>

<section class="edge">
  <div class="edge-text">
    <h2>Our Edge</h2>
    <p>Lorem ipsum dolor sit amet, consectetur adipiscing elit, sed do eiusmod tempor incididunt ut labore et dolore magna aliqua. Ut enim ad minim veniam, quis nostrud exercitation ullamco laboris nisi ut aliquip ex ea commodo consequat. Duis aute irure reprehenderit in voluptate velit esse cillum dolore eu fugiat nulla pariatur. Excepteur sint occaecat cupidatat.</p>
    <p>Lorem ipsum dolor sit amet, consectetur adipiscing elit, sed do eiusmod tempor incididunt ut labore et dolore magna aliqua. Ut enim ad minim veniam, quis nostrud exercitation ullamco.</p>
    <span class="btn">Investor Information</span>
  </div>
  <div class="edge-bar"></div>
  <div class="edge-frame"></div>
  <div class="edge-photo" role="img" aria-label="Smiling couple with an agent holding house keys in a bright room"></div>
</section>

<section class="news">
  <div class="news-kicker">Stay Updated</div>
  <div class="news-title">Newsletter<br>sign up form</div>
  <svg class="news-plane" width="84" height="60" viewBox="0 0 84 60" fill="none" stroke="rgba(255,255,255,.6)" stroke-width="2"><path d="M2 26 82 2 60 56 38 36z"/><path d="M38 36 82 2M38 36l-4 18 12-12"/></svg>
  <div class="field-line" style="left:590px;width:200px">Email</div>
  <div class="field-line" style="left:826px;width:196px">Name</div>
  <svg style="position:absolute;left:1062px;top:98px" width="24" height="18" viewBox="0 0 24 18" fill="none" stroke="#fff" stroke-width="2.4"><path d="M0 9h21M14 2l7 7-7 7"/></svg>
</section>

<section class="resp">
  <div class="resp-bar"></div>
  <div class="resp-frame"></div>
  <div class="resp-photo" role="img" aria-label="Young couple reviewing documents with an advisor outside a house"></div>
  <div class="resp-text">
    <h2>Our Responsibility</h2>
    <p>Lorem ipsum dolor sit amet, consectetur adipiscing elit, sed do eiusmod tempor incididunt ut labore et dolore magna aliqua. Ut enim ad minim veniam, quis nostrud exercitation ullamco laboris nisi ut aliquip ex ea commodo consequat. Duis aute irure reprehenderit in voluptate velit esse cillum dolore eu fugiat nulla pariatur. Excepteur sint occaecat.</p>
    <p>Lorem ipsum dolor sit amet, consectetur adipiscing elit, sed do eiusmod tempor incididunt ut labore et dolore magna aliqua. Ut enim ad minim veniam, quis nostrud exercitation ullamco.</p>
    <span class="btn">Read More</span>
  </div>
</section>

<section class="contact">
  <h2>Get In Touch</h2>
  <p class="lead">Lorem ipsum dolor sit amet, consectetur adipiscing elit, sed do eiusmod tempor incididunt ut labore et dolore magna aliqua. Ut enim ad minim.</p>
  <div class="form">
    <div class="input" style="top:0;left:0">First Name</div>
    <div class="input" style="top:0;left:392px">Last Name</div>
    <div class="input" style="top:64px;left:0">Email Address</div>
    <div class="input" style="top:64px;left:392px">Phone Number</div>
    <div class="input" style="top:128px;left:0;width:744px;height:84px">Message</div>
    <span class="btn">SUBMIT</span>
  </div>
</section>

<footer class="site-foot">
  <div class="foot-col" style="left:112px">
    <h4>IMPORTANT LINKS</h4>
    <a>About Us</a><a>Our Businesses</a><a>Investor Lobby</a><a>News</a><a>Contact Us</a>
  </div>
  <div class="foot-col" style="left:336px">
    <h4>EXPLORE VELTORA REAL ESTATE</h4>
    <a>About Us</a><a>Our Businesses</a><a>Investor Lobby</a>
  </div>
  <div class="foot-col" style="left:600px">
    <h4>CONTACT DETAILS</h4>
    <div class="contact-row"><svg width="14" height="14" viewBox="0 0 14 14"><path d="M3 1l3 3-2 2c1 2 2 3 4 4l2-2 3 3-2 2C6 13 1 8 1 3z" fill="#3fb9f2"/></svg>+1 888 888 8888</div>
    <div class="contact-row"><svg width="14" height="12" viewBox="0 0 14 12"><rect x="1" y="1" width="12" height="10" fill="none" stroke="#3fb9f2" stroke-width="1.6"/><path d="M1 1l6 5 6-5" fill="none" stroke="#3fb9f2" stroke-width="1.6"/></svg>info@veltorarealestate.com</div>
    <div class="contact-row"><svg width="12" height="14" viewBox="0 0 12 14"><path d="M6 14C2 9 1 7 1 5a5 5 0 0 1 10 0c0 2-1 4-5 9z" fill="#3fb9f2"/><circle cx="6" cy="5" r="2" fill="#fff"/></svg>1220, Lorem ipsum dolor sit amet,</div>
    <div class="contact-row" style="padding-left:22px">consectetur adipiscing elit</div>
  </div>
  <div class="socials"><i></i><i></i><i></i><i></i></div>
  <div class="legal">© 2022 All Rights Reserved &nbsp;|&nbsp; Legal Policy &nbsp;|&nbsp; Terms &amp; Conditions</div>
</footer>

</body>
</html>
```